Book Cover Project

This is a printed journal front and back cover design. We like the current design, but it feels a little too flat / too simple.

NOTE: we are not looking for a total makeover, just a finishing / polishing of this cover.

Here is our other book cover: https://www.shelvora-books.example/Quiet-Studio-Ledger-Fine-Morning/dp/7093268415/ref=tmm_hrd_swatch_0?_encoding=UTF8&qid=&sr=
it's purple and yellow (mostly purple)
this one is yellow and we're thinking to add a purple bar at the bottom

Specs: 6 in x 9 in full bleed for print

```html
<!DOCTYPE html>
<html lang="en">
<head>
<meta charset="utf-8">
<title>Steady Strides Logbook — Cover</title>
<link href="https://fonts.googleapis.com/css2?family=Arimo:wght@400;700&display=swap" rel="stylesheet">
<style>
  :root {
    --cover-yellow: #fdd500;
    --band-purple: #5a58a6;
    --ink: #0d0d0d;
    --runner-purple: #5d5ab0;
  }
  html, body {
    margin: 0;
    padding: 0;
    width: 805px;
    height: 1200px;
    overflow: hidden;
    background: var(--cover-yellow);
  }
  .cover {
    position: relative;
    width: 805px;
    height: 1200px;
    background: var(--cover-yellow);
    font-family: "Arimo", Arial, sans-serif;
    overflow: hidden;
  }
  .tagline-band {
    position: absolute;
    left: 0; top: 0;
    width: 805px; height: 77px;
    background: var(--band-purple);
    display: flex;
    align-items: center;
    justify-content: center;
  }
  .tagline {
    margin: 0;
    color: var(--cover-yellow);
    font-size: 37px;
    font-weight: 400;
    letter-spacing: 8px;
    white-space: nowrap;
  }
  .runner-illustration {
    position: absolute;
    left: 436px; top: 112px;
    width: 298px; height: 740px;
    border-radius: 130px 130px 60px 60px;
    background: linear-gradient(180deg, var(--runner-purple) 0%, #6f6cb8 60%, rgba(111,108,184,0.25) 100%);
  }
  .title {
    position: absolute;
    left: 0; top: 0;
    width: 805px; height: 1200px;
    pointer-events: none;
  }
  .title text {
    fill: var(--ink);
    font-family: "Arimo", Arial, sans-serif;
    font-size: 139px;
  }
  .title .title-bold { font-weight: 700; }
  .title .title-light { font-weight: 400; }
  .author-band {
    position: absolute;
    left: 0; bottom: 0;
    width: 805px; height: 89px;
    background: var(--band-purple);
    display: flex;
    align-items: center;
    justify-content: center;
  }
  .author {
    margin: 0;
    color: var(--cover-yellow);
    font-size: 46px;
    font-weight: 400;
    letter-spacing: 9px;
    white-space: nowrap;
  }
</style>
</head>
<body>
  <main class="cover">
    <header class="tagline-band">
      <p class="tagline">PACE - REFLECT - RENEW</p>
    </header>

    <div class="runner-illustration" role="img" aria-label="Single-line drawing of a runner in a purple vest and purple shorts, mid-stride"></div>

    <svg class="title" viewBox="0 0 805 1200" role="heading" aria-level="1" aria-label="Steady Strides Logbook">
      <text class="title-bold" x="48" y="853">STEADY</text>
      <text class="title-bold" x="48" y="966">STRIDES</text>
      <text class="title-light" x="48" y="1075">LOGBOOK</text>
    </svg>

    <footer class="author-band">
      <p class="author">ELIAS BRANDWOOD</p>
    </footer>
  </main>
</body>
</html>
```